Simple landing page for Brambles cookbook

I need a one page landingpage where customers can order the cookbook.
This is a cookbook of a collection of recipes from our deli that we used to run.
I need a landing page where customers can come and order the book. I also need it coded. I already have the domain through hostwell.
I can send the file of the book through wetransfer. It's too big to upload here. Just so you get the feel that I am looking for.
I attached a simple text as an introduction to the page. But I am open to any suggestions. I want it all to be about the experience that we are sharing the recipes with everybody and that it's for sale. The book is $29.99, shipping included.
Customers have to be able to click and buy the book from it.

Coding

Coded - Design and coding required

Number of Pages Required

1 page

Font styles to use
Sans Serif

Requirements
Must have
• Same colors as the cookbook

```html
<!DOCTYPE html>
<html lang="en">
<head>
<meta charset="utf-8">
<title>Brambles Cookbook</title>
<link href="https://fonts.googleapis.com/css2?family=Oswald:wght@500;700&family=Montserrat:wght@400;500&family=Comfortaa:wght@500&display=swap" rel="stylesheet">
<style>
  :root {
    --green: #7f9e3b;
    --green-soft: #bfcc93;
    --cream: #f3f1e2;
    --brown-dark: #4a2e1b;
    --taupe: #8a786b;
    --white: #ffffff;
    --ink: #2f2a26;
  }
  * { margin: 0; padding: 0; box-sizing: border-box; }
  html, body { width: 701px; height: 1200px; overflow: hidden; background: var(--white); }
  .page { position: relative; width: 701px; height: 1200px; overflow: hidden; font-family: "Montserrat", sans-serif; color: var(--ink); }
  .backdrop { position: absolute; left: 0; top: 0; width: 701px; height: 1200px; }
  .brand { position: absolute; left: 85px; top: 14px; display: flex; align-items: center; gap: 6px; }
  .brand-dot { width: 12px; height: 12px; border-radius: 50%; background: var(--green); }
  .brand-name { font-family: "Oswald", sans-serif; font-weight: 700; font-size: 22px; letter-spacing: 0.5px; color: var(--brown-dark); }
  .hero-title { position: absolute; left: 85px; top: 106px; width: 300px; font-family: "Oswald", sans-serif; font-weight: 700; font-size: 20px; line-height: 30px; letter-spacing: 0.6px; color: var(--brown-dark); text-transform: uppercase; }
  .includes { position: absolute; left: 85px; top: 207px; font-size: 10px; font-weight: 500; letter-spacing: 1px; color: var(--ink); }
  .includes strong { font-weight: 500; font-size: 12.5px; color: var(--green); }
  .categories { position: absolute; left: 85px; top: 229px; display: flex; gap: 17px; font-size: 8px; letter-spacing: 0.5px; }
  .category { display: flex; align-items: center; gap: 5px; }
  .category svg { width: 12px; height: 10px; }
  .btn { position: absolute; width: 89px; height: 22px; border-radius: 11px; background: var(--green); color: var(--white); font-family: "Oswald", sans-serif; font-weight: 500; font-size: 9.5px; letter-spacing: 1px; display: flex; align-items: center; justify-content: center; text-decoration: none; box-shadow: 0 3px 6px rgba(0,0,0,0.18); }
  .btn-hero { left: 85px; top: 256px; }
  .btn-offer { left: 451px; top: 893px; }
  .book-art { position: absolute; border-radius: 2px; }
  .book-hero { left: 440px; top: 46px; width: 172px; height: 276px; background: linear-gradient(180deg, #f4f4f2 0%, #e9e8e4 42%, #8e8172 62%, #4c4a46 80%, #dcdcd8 100%); box-shadow: 6px 14px 24px rgba(0,0,0,0.18); }
  .book-pair { left: 40px; top: 676px; width: 300px; height: 316px; background: linear-gradient(180deg, #e2e2e0 0%, #cfcfcc 40%, #8a7a68 58%, #3f3e3b 78%, #cfcfcc 100%); border-radius: 4px; box-shadow: 8px 14px 24px rgba(0,0,0,0.18); }
  .badge { position: absolute; width: 70px; height: 70px; }
  .badge-hero { left: 405px; top: 104px; }
  .badge-offer { left: 461px; top: 716px; }
  .badge-text { position: absolute; left: 0; top: 14px; width: 70px; text-align: center; color: var(--white); }
  .badge-price { font-family: "Oswald", sans-serif; font-weight: 500; font-size: 18px; line-height: 20px; }
  .badge-price small { font-size: 9px; }
  .badge-ship { display: flex; align-items: center; justify-content: center; gap: 3px; font-size: 5px; line-height: 6px; text-align: left; margin-top: 2px; }
  .story-card { position: absolute; left: 85px; top: 396px; width: 533px; height: 224px; border-radius: 8px; background: var(--taupe); overflow: hidden; box-shadow: 0 6px 16px rgba(0,0,0,0.2); }
  .story-photo { position: absolute; left: 0; top: 0; width: 276px; height: 224px; background: radial-gradient(ellipse at 45% 45%, #8a4d22 0%, #a86a35 38%, #d9a15a 55%, #e9e6e0 70%, #b27a44 100%); }
  .story-text { position: absolute; left: 306px; top: 38px; width: 215px; font-family: "Oswald", sans-serif; font-weight: 500; font-size: 13px; line-height: 20.5px; letter-spacing: 1px; color: var(--white); }
  .offer-title { position: absolute; left: 360px; top: 786px; width: 270px; text-align: center; font-family: "Oswald", sans-serif; font-weight: 700; font-size: 29px; line-height: 30px; letter-spacing: 2px; color: var(--brown-dark); }
  .offer-sub { position: absolute; left: 380px; top: 857px; width: 230px; text-align: center; font-size: 7.8px; line-height: 11.5px; letter-spacing: 0.6px; color: var(--ink); }
  .quote-card { position: absolute; left: 85px; top: 1024px; width: 532px; height: 128px; border-radius: 8px; background: var(--taupe); }
  .quote-mark { position: absolute; left: 247px; top: -18px; width: 36px; height: 36px; border-radius: 50%; background: var(--green); color: var(--white); font-family: "Oswald", sans-serif; font-size: 26px; line-height: 44px; text-align: center; }
  .quote-text { position: absolute; left: 60px; top: 40px; width: 412px; text-align: center; font-family: "Comfortaa", sans-serif; font-weight: 500; font-size: 10.5px; line-height: 17.5px; letter-spacing: 1px; color: var(--white); }
  .copyright { position: absolute; left: 0; top: 1176px; width: 701px; text-align: center; font-size: 8.3px; color: var(--ink); }
</style>
</head>
<body>
<main class="page">
  <svg class="backdrop" viewBox="0 0 701 1200" aria-hidden="true">
    <defs>
      <linearGradient id="heroWash" x1="0" y1="0" x2="0" y2="1">
        <stop offset="0" stop-color="#bfcc93"/>
        <stop offset="0.45" stop-color="#e3e5cc"/>
        <stop offset="1" stop-color="#ffffff"/>
      </linearGradient>
      <linearGradient id="offerWash" x1="0" y1="0" x2="1" y2="1">
        <stop offset="0" stop-color="#bfcc93"/>
        <stop offset="0.6" stop-color="#d3dbb0"/>
        <stop offset="1" stop-color="#eeeed9"/>
      </linearGradient>
    </defs>
    <path d="M0 100 C70 70 140 58 210 64 C300 72 380 120 470 150 C560 170 640 150 701 138 L701 420 L0 420 Z" fill="url(#heroWash)"/>
    <path d="M20 116 C50 92 80 76 115 63" stroke="#ffffff" stroke-width="3" fill="none"/>
    <path d="M0 604 C90 680 200 736 340 752 C480 752 600 720 701 690 L701 962 L510 962 C620 945 670 910 682 886 C600 930 470 952 330 930 C200 910 100 900 0 896 Z" fill="url(#offerWash)"/>
  </svg>

  <header class="brand">
    <span class="brand-dot"></span>
    <span class="brand-name">BRAMBLES</span>
  </header>

  <h1 class="hero-title">It's finally here! The Brambles cookbook with all your favourite recipes</h1>
  <p class="includes">BOOK INCLUDES <strong>28 RECIPES:</strong></p>
  <ul class="categories">
    <li class="category"><svg viewBox="0 0 12 10"><path d="M1 6 L6 2 L11 6 Z M1 8 H11" stroke="#7f9e3b" fill="none"/></svg>Sandwiches</li>
    <li class="category"><svg viewBox="0 0 12 10"><path d="M1 4 H9 L7 8 H3 Z M9 4 L11 2" stroke="#7f9e3b" fill="none"/></svg>Sauces</li>
    <li class="category"><svg viewBox="0 0 12 10"><path d="M2 5 C2 2 10 2 10 5 Z M2 7 H10 M3 9 H9" stroke="#7f9e3b" fill="none"/></svg>Burgers</li>
  </ul>
  <a class="btn btn-hero" href="#order">ORDER NOW</a>

  <div class="book-art book-hero" role="img" aria-label="Brambles cookbook cover: restaurant counter with an order-here chalkboard"></div>

  <div class="badge badge-hero">
    <svg viewBox="0 0 70 70" width="70" height="70" aria-hidden="true"><polygon fill="#7f9e3b" points="35,0 43,7 53,5 56,15 65,20 62,30 70,35 62,40 65,50 56,55 53,65 43,63 35,70 27,63 17,65 14,55 5,50 8,40 0,35 8,30 5,20 14,15 17,5 27,7"/></svg>
    <div class="badge-text">
      <div class="badge-price"><small>$</small>29.99</div>
      <div class="badge-ship"><svg width="12" height="7" viewBox="0 0 12 7"><path d="M0.5 0.5 H7.5 V5 H0.5 Z M7.5 2 H10 L11.5 4 V5 H7.5" stroke="#fff" fill="none" stroke-width="0.8"/></svg><span>Free<br>Shipping</span></div>
    </div>
  </div>

  <section class="story-card">
    <div class="story-photo" role="img" aria-label="Salted pretzel sandwich with cheese on a white plate"></div>
    <p class="story-text">We can't open another Brambles restaurant but we can offer you this compilation of our best recipies for you to make and enjoy at home. Storefront picture beside it or something like that.</p>
  </section>

  <div class="book-art book-pair" role="img" aria-label="Two copies of the Brambles cookbook"></div>

  <div class="badge badge-offer">
    <svg viewBox="0 0 70 70" width="70" height="70" aria-hidden="true"><polygon fill="#7f9e3b" points="35,0 43,7 53,5 56,15 65,20 62,30 70,35 62,40 65,50 56,55 53,65 43,63 35,70 27,63 17,65 14,55 5,50 8,40 0,35 8,30 5,20 14,15 17,5 27,7"/></svg>
    <div class="badge-text">
      <div class="badge-price"><small>$</small>29.99</div>
      <div class="badge-ship"><svg width="12" height="7" viewBox="0 0 12 7"><path d="M0.5 0.5 H7.5 V5 H0.5 Z M7.5 2 H10 L11.5 4 V5 H7.5" stroke="#fff" fill="none" stroke-width="0.8"/></svg><span>Free<br>Shipping</span></div>
    </div>
  </div>

  <h2 class="offer-title">FAVORITE RECIPES<br>IN ONE BOOK</h2>
  <p class="offer-sub">We Truly Hope You Will Enjoy Making These Sandwiches Just As Much As We Did.</p>
  <a class="btn btn-offer" id="order" href="#order">ORDER NOW</a>

  <section class="quote-card">
    <div class="quote-mark">&#8221;</div>
    <p class="quote-text">We can't open another Brambles, but we can offer you this collection of our recipes for you to try out at home with your family and friends.</p>
  </section>

  <footer class="copyright">Copyright 2022. Marta Linden | All Rights Reserved</footer>
</main>
</body>
</html>
```